Create website for home automation - Control your lighting, fans, blinds etc remotely by smartphone

Plan for SHOPIFY Website - Our Clever Dwelling
Company name: Our Clever Dwelling
Company Slogan: Calm Evenings Come Naturally
Clean, Modern, Easy to Navigate, easy to maintain - not a lot of coding. We need flash technology but displaying simply what we do.
What we provide:
We will be offering wireless switch which can be added to iOS/Android App via WiFi, allowing users to remotely turn on/off connected lights, fans, security cameras, appliances, irrigation, humidifier separately from anywhere at any time.
Control your home away from home. No more wandering of your mind on those lights or appliances which you might have left switched on. No need to drive back home to check and switch them off. Save that energy, money and time just with a click of your phone no matter how far you are from home.
Replace your home electrical switches with smart switches. They retrofit existing electrical switches and allow you to make the transformation as needed.
Easy to use and intuitive app allows you to control your lights and devices just at a click. Set any kind of ambiance suiting your occasion.
Set scenes in smartphone app to group and operate your devices just at a button click. Same device can be included in more than one scene.
Collections and Products
Light Switches
Wall Plugs
Fan Switch
Pendants etc special lighting types.
Light Dimmers
Blind Controllers
Home Page:
Home page needs to telling customers what we do and how we do it in a few words to grab people.
Phone
Email
Support – Download instructions per product
Client login
Wholesale login
Promotional video to be on home screen - this is a short 1.5 - 2 min illustration introduction video to who we are and what we do - this is yet to be created)
Social media link - Friendwall
Pages:
FAQ
About Us
Support/Shipping/Returns policy
Support/Installation
Blog posts
Product pages:
Description
Price
Space for where a video will be featured - how each product works/installation.
Reviews
Our competition:
http://www.brivo.com.au
https://lumigardenhub.com.au/2018/04/05/best-smart-light-switches-and-plugs/
https://www.tavelinq.com

```html
<!DOCTYPE html>
<html lang="en">
<head>
<meta charset="utf-8">
<title>Our Clever Dwelling</title>
<link href="https://fonts.googleapis.com/css2?family=Roboto:wght@400;500;700&display=swap" rel="stylesheet">
<style>
:root{
  --navy:#1d2b5c;
  --blue:#1f56b0;
  --pink:#e0237a;
  --ink:#2b2b2b;
  --muted:#555;
  --line:#e3e3e3;
  --soft:#f6f6f6;
  --white:#fff;
  --foot-a:#17276a;
  --foot-b:#0f4da6;
}
*{margin:0;padding:0;box-sizing:border-box}
html,body{width:1200px;height:4380px;overflow:hidden;background:var(--white)}
body{position:relative;font-family:'Roboto',Arial,sans-serif;color:var(--ink)}
.abs{position:absolute}
.photo{position:absolute}
p.body-copy{font-size:14px;line-height:26px;color:var(--muted)}

/* header & hero */
.hero{left:0;top:0;width:1200px;height:675px;background:linear-gradient(135deg,#3a3128 0%,#6b5a48 40%,#2c2620 75%,#15120f 100%)}
.hero-shade{left:0;top:0;width:1200px;height:675px;background:rgba(0,0,0,.35)}
.brand{left:146px;top:58px;width:200px;text-align:center;color:var(--white)}
.brand-name{font-size:17px;font-weight:700;letter-spacing:.5px;text-transform:uppercase}
.brand-tag{font-size:10px;letter-spacing:1px;margin-top:4px}
.brand-dot{display:block;width:34px;height:34px;border-radius:50%;border:2px solid var(--white);margin:0 auto 8px}
.nav{left:403px;top:66px;display:flex;gap:28px;color:var(--white);font-size:15px;font-weight:500}
.nav-icons{left:980px;top:58px;display:flex;gap:18px}
.hero-title{left:0;top:280px;width:1200px;text-align:center;color:var(--white);font-size:58px;font-weight:700}
.hero-sub{left:0;top:352px;width:1200px;text-align:center;color:var(--white);font-size:36px;font-weight:400}
.btn-solid{background:var(--blue);color:var(--white);border-radius:24px;font-size:15px;font-weight:700;text-align:center;text-transform:uppercase}
.hero-btn{left:520px;top:418px;width:160px;height:46px;line-height:46px}

/* partner strip */
.partners{left:0;top:675px;width:1200px;height:120px;background:#f3f3f3;border-top:1px solid var(--line);border-bottom:1px solid var(--line)}
.partner{position:absolute;top:40px;height:38px;background:#c9c9c9;border-radius:4px}

/* intro blocks */
.h2{font-size:38px;font-weight:700;color:var(--navy);text-transform:uppercase}
.btn-outline{border:2px solid var(--blue);color:var(--blue);border-radius:20px;font-size:16px;font-weight:500;text-align:center;height:40px;line-height:36px}
.framed{box-shadow:0 6px 18px rgba(0,0,0,.25);border:6px solid var(--white)}

/* video band */
.video{left:0;top:1740px;width:1200px;height:538px;background:linear-gradient(180deg,#7f7a72 0%,#a8a197 50%,#5e5a53 100%)}
.video-shade{left:0;top:1740px;width:1200px;height:538px;background:rgba(0,0,0,.25)}
.video-title{left:0;top:1906px;width:1200px;text-align:center;color:var(--white);font-size:46px;font-weight:400}

/* features */
.feature{width:330px;text-align:center}
.feature h3{font-size:24px;font-weight:500;color:var(--ink);margin-top:24px}
.feature p{font-size:13px;line-height:24px;color:var(--muted);margin-top:14px;padding:0 20px}

/* collections */
.collections{left:0;top:2680px;width:1200px;height:600px;background:var(--soft);border-top:1px solid var(--line)}
.thumb{position:absolute;top:3121px;width:70px;height:56px;border:3px solid var(--white)}
.h2-plain{font-size:40px;font-weight:500;color:var(--ink)}
.btn-pink{background:var(--pink);color:var(--white);font-size:15px;font-weight:700;text-transform:uppercase;text-align:center;height:38px;line-height:38px}

/* instagram */
.section-title{width:1200px;left:0;text-align:center;font-size:28px;font-weight:700;color:var(--ink);text-transform:uppercase}
.insta{position:absolute;top:3428px;width:138px;height:149px}

/* newsletter */
.news-input{left:295px;top:3784px;width:464px;height:46px;border:1px solid #cfcfcf;border-radius:23px;background:var(--white);font-size:11px;color:#777;padding:16px 24px}
.news-btn{left:774px;top:3784px;width:131px;height:46px;line-height:46px;font-size:15px}

/* footer */
.footer{left:0;top:3922px;width:1200px;height:458px;background:linear-gradient(90deg,var(--foot-a),var(--foot-b))}
.foot-col{top:3982px;color:var(--white)}
.foot-col h4{font-size:17px;font-weight:700;text-transform:uppercase;margin-bottom:20px}
.foot-col h4.cap{text-transform:none}
.foot-col li{list-style:none;font-size:13px;line-height:27px;color:#dfe6f5}
.social li,.contact li{display:flex;align-items:center;gap:10px;line-height:34px}
.ring{width:22px;height:22px;border:1.5px solid #dfe6f5;border-radius:50%;flex:none}
.contact li{align-items:flex-start;line-height:20px;margin-bottom:12px}
.foot-rule{left:0;top:4292px;width:1200px;height:1px;background:rgba(255,255,255,.2)}
.copyright{left:0;top:4322px;width:1200px;text-align:center;font-size:13px;color:#dfe6f5}
</style>
</head>
<body>

<!-- Header & hero -->
<div class="photo hero" role="img" aria-label="Person holding a tablet home controller in a softly lit living room"></div>
<div class="abs hero-shade"></div>
<div class="abs brand">
  <span class="brand-dot"></span>
  <div class="brand-name">Our Clever Dwelling</div>
  <div class="brand-tag">Calm Evenings Come Naturally</div>
</div>
<nav class="abs nav"><span>HOME</span><span>ABOUT US</span><span>PRODUCTS</span><span>SUPPORT</span><span>BLOG</span><span>FAQ</span><span>CONTACT</span></nav>
<div class="abs nav-icons">
  <svg width="26" height="26" viewBox="0 0 26 26"><circle cx="11" cy="11" r="8" fill="none" stroke="#fff" stroke-width="3"/><line x1="17" y1="17" x2="24" y2="24" stroke="#fff" stroke-width="3"/></svg>
  <svg width="24" height="26" viewBox="0 0 24 26"><rect x="2" y="8" width="20" height="17" rx="2" fill="#fff"/><path d="M7 9V6a5 5 0 0 1 10 0v3" fill="none" stroke="#fff" stroke-width="2.5"/></svg>
</div>
<h1 class="abs hero-title">OUR CLEVER DWELLING</h1>
<div class="abs hero-sub">Calm Evenings Come Naturally</div>
<div class="abs btn-solid hero-btn">Read More</div>

<!-- Partner strip -->
<div class="abs partners">
  <div class="partner" style="left:168px;width:64px"></div>
  <div class="partner" style="left:282px;width:104px"></div>
  <div class="partner" style="left:444px;width:92px"></div>
  <div class="partner" style="left:596px;width:104px"></div>
  <div class="partner" style="left:776px;width:76px"></div>
  <div class="partner" style="left:918px;width:112px"></div>
</div>

<!-- What we do -->
<h2 class="abs h2" style="left:146px;top:908px">What We Do</h2>
<p class="abs body-copy" style="left:146px;top:976px;width:450px">Sed ut perspiciatis unde omnis iste natus error sit voluptatem accusantium doloremque laudantium, totam rem aperiam, eaque ipsa quae ab illo inventore veritatis et quasi architecto beatae vitae dicta sunt explicabo. Nemo enim ipsam voluptatem quia voluptas sit aspernatur aut odit aut fugit, sed quia consequuntur</p>
<div class="abs btn-outline" style="left:146px;top:1145px;width:140px">Read More</div>
<div class="photo framed" style="left:634px;top:885px;width:423px;height:327px;background:linear-gradient(135deg,#e8e6e2,#bfb9b0 60%,#3f4a63)" role="img" aria-label="Woman pressing a wall-mounted smart home control panel"></div>

<!-- How we do it -->
<div class="photo framed" style="left:143px;top:1285px;width:420px;height:327px;background:linear-gradient(135deg,#8a6a4c,#d9cbb6 50%,#3b3a3f)" role="img" aria-label="Hand holding a smartphone with a home control app in front of a modern interior"></div>
<h2 class="abs h2" style="left:616px;top:1303px">How We Do It</h2>
<p class="abs body-copy" style="left:616px;top:1364px;width:450px">Sed ut perspiciatis unde omnis iste natus error sit voluptatem accusantium doloremque laudantium, totam rem aperiam, eaque ipsa quae ab illo inventore veritatis et quasi architecto beatae vitae dicta sunt explicabo. Nemo enim ipsam voluptatem quia voluptas sit aspernatur aut odit aut fugit, sed quia consequuntur</p>
<div class="abs btn-outline" style="left:613px;top:1542px;width:143px">Read More</div>

<!-- Video band -->
<div class="photo video" role="img" aria-label="Hands holding a phone with a remote home control app in a bright kitchen"></div>
<div class="abs video-shade"></div>
<div class="abs video-title">Calm Evenings Come Naturally</div>
<svg class="abs" style="left:563px;top:1990px" width="72" height="72" viewBox="0 0 72 72"><circle cx="36" cy="36" r="34" fill="#fff"/><circle cx="36" cy="36" r="28" fill="none" stroke="#222" stroke-width="3"/><path d="M30 24 L48 36 L30 48 Z" fill="#222"/></svg>

<!-- Features -->
<div class="abs feature" style="left:104px;top:2360px">
  <svg width="96" height="100" viewBox="0 0 96 100"><rect x="4" y="4" width="88" height="92" fill="none" stroke="#1f56b0" stroke-width="4"/><rect x="22" y="22" width="52" height="56" fill="none" stroke="#1f56b0" stroke-width="3"/><line x1="48" y1="22" x2="48" y2="78" stroke="#1f56b0" stroke-width="3"/><line x1="34" y1="46" x2="34" y2="54" stroke="#1f56b0" stroke-width="3"/><line x1="62" y1="46" x2="62" y2="54" stroke="#1f56b0" stroke-width="3"/></svg>
  <h3>Light Switches</h3>
  <p>Sed ut perspiciatis unde omnis iste natus error sit voluptatem accusantium doloremque laudantium, totam rem aperiam</p>
</div>
<div class="abs feature" style="left:434px;top:2360px">
  <svg width="96" height="100" viewBox="0 0 96 100"><rect x="4" y="4" width="88" height="92" fill="none" stroke="#1f56b0" stroke-width="4"/><rect x="32" y="18" width="32" height="64" fill="none" stroke="#1f56b0" stroke-width="3"/><circle cx="48" cy="38" r="6" fill="none" stroke="#1f56b0" stroke-width="3"/><rect x="42" y="54" width="12" height="16" fill="none" stroke="#1f56b0" stroke-width="3"/></svg>
  <h3>Light Dimmers</h3>
  <p>Sed ut perspiciatis unde omnis iste natus error sit voluptatem accusantium doloremque laudantium, totam rem aperiam</p>
</div>
<div class="abs feature" style="left:764px;top:2360px">
  <svg width="100" height="100" viewBox="0 0 100 100"><g fill="none" stroke="#1f56b0" stroke-width="3"><rect x="38" y="38" width="24" height="24" transform="rotate(45 50 50)"/><line x1="62" y1="30" x2="74" y2="18"/><line x1="70" y1="38" x2="82" y2="26"/><path d="M34 66 L20 80 Q12 90 20 96"/></g></svg>
  <h3>Wall Plugs</h3>
  <p>Sed ut perspiciatis unde omnis iste natus error sit voluptatem accusantium doloremque laudantium, totam rem aperiam</p>
</div>

<!-- Collections -->
<div class="abs collections"></div>
<div class="photo" style="left:143px;top:2760px;width:409px;height:335px;background:linear-gradient(180deg,#ffffff 0%,#dfeef7 50%,#8cc63f 80%,#e8f0f4 100%);border:1px solid #d6d6d6" role="img" aria-label="Illustration of a connected house on a lawn above a tablet with control icons"></div>
<div class="thumb" style="left:193px;background:linear-gradient(135deg,#bfe3f2,#7cb342)" role="img" aria-label="Connected house illustration thumbnail"></div>
<div class="thumb" style="left:272px;background:linear-gradient(135deg,#3d4b6b,#9aa7bd)" role="img" aria-label="Smart device thumbnail"></div>
<div class="thumb" style="left:350px;background:linear-gradient(135deg,#c9c2b7,#5f6b80)" role="img" aria-label="Control panel thumbnail"></div>
<div class="thumb" style="left:432px;background:linear-gradient(135deg,#1e3a78,#4f7bd1)" role="img" aria-label="App screen thumbnail"></div>
<h2 class="abs h2-plain" style="left:593px;top:2758px">Collections and Products</h2>
<p class="abs body-copy" style="left:593px;top:2826px;width:460px">Sed ut perspiciatis unde omnis iste natus error sit voluptatem accusantium doloremque laudantium, totam rem aperiam, eaque ipsa quae ab illo inventore veritatis et quasi architecto beatae vitae dicta sunt explicabo. Nemo enim ipsam voluptatem quia voluptas sit aspernatur aut odit aut fugit, sed quia consequuntur magni dolores eos qui ratione voluptatem sequi nesciunt. Neque porro quisquam est, qui dolorem ipsum quia dolor sit amet, consectetur, adipisci velit, sed quia</p>
<div class="abs btn-pink" style="left:593px;top:3060px;width:397px">Download Instructions per Product</div>

<!-- Instagram -->
<h2 class="abs section-title" style="top:3346px">Instagram</h2>
<div class="insta" style="left:143px;background:linear-gradient(135deg,#d8d6d0,#6f6a60)" role="img" aria-label="Wall mounted smart thermostat photo"></div>
<div class="insta" style="left:298px;background:linear-gradient(135deg,#1b1f3a,#c98a2b)" role="img" aria-label="Tablet controlling lights at night"></div>
<div class="insta" style="left:453px;background:linear-gradient(135deg,#e9e6e1,#4b5a73)" role="img" aria-label="Man using a smartphone at home"></div>
<div class="insta" style="left:607px;background:linear-gradient(135deg,#cfe4f2,#6aa84f)" role="img" aria-label="Family relaxing in a connected home"></div>
<div class="insta" style="left:762px;background:linear-gradient(135deg,#eeeeec,#a7a39b)" role="img" aria-label="Couple on a sofa with a tablet"></div>
<div class="insta" style="left:916px;background:linear-gradient(135deg,#f0efed,#7c7a77)" role="img" aria-label="Man beside window blinds holding a phone"></div>

<!-- Newsletter -->
<h2 class="abs section-title" style="top:3650px">Join Our Newsletter</h2>
<p class="abs body-copy" style="left:260px;top:3700px;width:680px;text-align:center;font-size:15px;line-height:26px">Sed ut perspiciatis unde omnis iste natus error sit voluptatem accusantium doloremque laudantium, totam rem aperiam, eaque ipsa quae ab illo inventore veritatis</p>
<div class="abs news-input">Enter Your Email</div>
<div class="abs btn-solid news-btn">Join Now</div>

<!-- Footer -->
<footer class="abs footer"></footer>
<div class="abs foot-col" style="left:143px">
  <h4>Quick Links</h4>
  <ul><li>About Us</li><li>Products</li><li>Support</li><li>Blog</li><li>FAQ</li><li>Contact</li><li>Client login</li><li>Wholesale login</li></ul>
</div>
<div class="abs foot-col" style="left:350px">
  <h4 class="cap">Products</h4>
  <ul><li>Light Switches</li><li>Wall Plugs</li><li>Fan Switch</li><li>Pendants etc special lighting types.</li><li>Light Dimmers</li><li>Blind Controllers</li></ul>
</div>
<div class="abs foot-col social" style="left:642px">
  <h4>Social</h4>
  <ul><li><span class="ring"></span>Friendwall</li><li><span class="ring"></span>Chirpline</li><li><span class="ring"></span>Plusring</li><li><span class="ring"></span>Clipstream</li></ul>
</div>
<div class="abs foot-col contact" style="left:794px">
  <h4>Contact Us</h4>
  <ul>
    <li><svg width="16" height="20" viewBox="0 0 16 20"><path d="M8 1a6 6 0 0 1 6 6c0 5-6 12-6 12S2 12 2 7a6 6 0 0 1 6-6z" fill="none" stroke="#dfe6f5" stroke-width="1.6"/><circle cx="8" cy="7" r="2" fill="#dfe6f5"/></svg><span>Our Clever Dwelling<br>Unit 7, 48 Harbour Lane<br>Location.</span></li>
    <li><svg width="16" height="18" viewBox="0 0 16 18"><path d="M3 1l3 1 1 4-2 1c1 3 3 5 6 6l1-2 4 1 1 3-2 2C7 17 0 10 1 3z" fill="#dfe6f5"/></svg><span>Phone : +61 2 5550 1842</span></li>
    <li><svg width="16" height="14" viewBox="0 0 16 14"><rect x="1" y="2" width="14" height="10" fill="none" stroke="#dfe6f5" stroke-width="1.5"/><path d="M1 2l7 6 7-6" fill="none" stroke="#dfe6f5" stroke-width="1.5"/></svg><span>info@ourcleverdwelling.com</span></li>
  </ul>
</div>
<div class="abs foot-rule"></div>
<div class="abs copyright">Copyright © Our Clever Dwelling. 2018. All rights reserved.</div>
<svg class="abs" style="left:1118px;top:4316px" width="20" height="14" viewBox="0 0 20 14"><path d="M7 2L2 7l5 5M13 2l5 5-5 5" fill="none" stroke="#dfe6f5" stroke-width="1.8"/></svg>

</body>
</html>
```